RW Framewell Inc Business cards

We need business cards using our existing logo but slightly modified. Right now the logo says RW Loadbearing Masonry. We want to keep the RW part of the design, but replace the Structural Concrete portion with "FRAMEWELL". Please see the attached file.
Ideally this would be a blank template so we can add Different Names, titles, and phone numbers later.
On the one side we want only the logo and on the other side the detail. I'm attaching an example for you to see.
Please reach out with any other questions. Our address and other details will be given out once we find a design we like.

Target Market(s)

Construction Industry

```html
<!DOCTYPE html>
<html lang="en">
<head>
<meta charset="utf-8">
<title>RW Framewell Inc Business Cards</title>
<link rel="stylesheet" href="https://fonts.googleapis.com/css2?family=Arimo:wght@400;700&display=swap">
<style>
  :root {
    --bg: #0c0c0d;
    --card: #2a2a2c;
    --card-back: #252527;
    --edge: #1e78c8;
    --blue: #1f7acb;
    --grey-text: #c9c9cb;
    --grey-mark: #5a5a5d;
    --rule: #4a4a4d;
  }
  * { margin: 0; padding: 0; box-sizing: border-box; }
  html, body {
    width: 1200px;
    height: 820px;
    overflow: hidden;
    background: var(--bg);
    font-family: "Arimo", Arial, sans-serif;
  }
  .sheet {
    position: relative;
    width: 1200px;
    height: 820px;
    display: flex;
    align-items: center;
    justify-content: center;
    gap: 40px;
  }
  .card {
    position: relative;
    width: 540px;
    height: 309px;
    background: var(--card);
    border-left: 3px solid var(--edge);
    border-bottom: 3px solid var(--edge);
    box-shadow: 0 18px 40px rgba(0,0,0,0.6);
  }
  .card--back { background: var(--card-back); }

  .wordmark {
    font-weight: 700;
    text-transform: uppercase;
    letter-spacing: 1px;
    line-height: 1;
  }
  .card--front .wordmark {
    position: absolute;
    right: 40px;
    top: 36px;
    color: var(--blue);
    font-size: 44px;
    text-align: right;
  }
  .card--front .wordmark span { display: block; font-size: 30px; margin-top: 6px; }

  .contact {
    position: absolute;
    left: 36px;
    right: 30px;
    top: 150px;
    color: var(--grey-text);
  }
  .contact__head {
    display: flex;
    align-items: center;
    gap: 14px;
  }
  .contact__name {
    flex: none;
    color: var(--blue);
    font-weight: 700;
    font-size: 19px;
    line-height: 22px;
    text-transform: uppercase;
    letter-spacing: 0.5px;
  }
  .divider {
    flex: 1;
    height: 1px;
    background: var(--rule);
  }
  .contact__title { font-size: 15px; line-height: 20px; margin-top: 2px; }
  .contact__list { list-style: none; margin-top: 16px; font-size: 15px; }
  .contact__list li { display: flex; align-items: center; gap: 10px; margin-top: 5px; line-height: 18px; }
  .contact__list svg { width: 16px; height: 16px; flex: none; }

  .website {
    position: absolute;
    right: 30px;
    top: 184px;
    font-size: 14px;
    line-height: 18px;
    color: var(--grey-text);
  }
  .website em { font-style: normal; color: var(--blue); }

  .card--back .wordmark {
    position: absolute;
    inset: 0;
    display: flex;
    flex-direction: column;
    align-items: center;
    justify-content: center;
    color: var(--grey-mark);
    font-size: 64px;
  }
  .card--back .wordmark span { font-size: 40px; margin-top: 10px; }
</style>
</head>
<body>
  <main class="sheet">
    <section class="card card--front" aria-label="Card front with contact details">
      <div class="wordmark">RW<span>Framewell</span></div>
      <div class="contact">
        <div class="contact__head">
          <p class="contact__name">Daniel Ashcombe</p>
          <div class="divider"></div>
        </div>
        <p class="contact__title">Managing Director</p>
        <ul class="contact__list">
          <li>
            <svg viewBox="0 0 16 16" aria-hidden="true">
              <rect x="0.75" y="0.75" width="14.5" height="14.5" rx="2" fill="none" stroke="#1f7acb" stroke-width="1.5"/>
              <path d="M5 4c-1 1-.8 3 1 5s4 2.5 5 1.5l-1.3-1.4-1.2.7c-.8-.3-1.8-1.3-2.1-2.1l.7-1.2z" fill="#1f7acb"/>
            </svg>
            055-810 274 396
          </li>
          <li>
            <svg viewBox="0 0 16 16" aria-hidden="true">
              <rect x="0.5" y="3" width="15" height="10" fill="#1f7acb"/>
              <path d="M0.5 3 8 9l7.5-6M0.5 13l5.5-5M15.5 13l-5.5-5" fill="none" stroke="#2a2a2c" stroke-width="1.2"/>
            </svg>
            hello@framewellbuild.com
          </li>
        </ul>
      </div>
      <div class="website">www.<em>framewellbuild</em>.com</div>
    </section>

    <section class="card card--back" aria-label="Card back with company name">
      <div class="wordmark">RW<span>Framewell</span></div>
    </section>
  </main>
</body>
</html>
```